Vorn upkeep KT Solar Venture

Solar power system install
Services and maintenance
wiring, Rewinding and Renovation
Switch Board Upgrade
Power and lighting point
t doesn’t matter how much you spend on quality parts, your solar system will let you down if your design and installation are sub-par. Have your solar system tailored and installed by our Master Electrician and Bright Grid Guild Accredited team.

Target Market(s)

sales and installed

Industry/Entity Type

Solar install and retailer

Contact Information for Business Card

Name , Email, Phone Number ,Business address,

Font styles to use
Serif

Colors
0054AA
0677BA
7BADD7
CADEEF
E8F1F8

Requirements
Must have
• clear and bright
Nice to have
• new design
Should not have
• unclear pictures

```html
<!DOCTYPE html>
<html lang="en">
<head>
<meta charset="utf-8">
<title>Vorn upkeep – KT Solar Venture business card</title>
<link rel="stylesheet" href="https://fonts.googleapis.com/css2?family=Roboto:wght@400;700&display=swap">
<style>
  :root {
    --stage: #2e2e2e;
    --blue-deep: #0054AA;
    --blue: #0677BA;
    --blue-soft: #7BADD7;
    --blue-pale: #CADEEF;
    --paper: #F1F2F2;
    --green: #2E9E3A;
    --ink: #1B1B1B;
    --white: #ffffff;
  }
  * { margin: 0; padding: 0; box-sizing: border-box; }
  html, body { width: 1200px; height: 1138px; overflow: hidden; background: var(--stage); }
  body { position: relative; font-family: "Roboto", Arial, sans-serif; }

  .card {
    position: absolute;
    border-radius: 14px;
    overflow: hidden;
  }
  .card-front { left: 274px; top: 186px; width: 623px; height: 376px; background: linear-gradient(160deg, var(--blue-deep) 0%, var(--blue) 100%); }
  .card-back  { left: 275px; top: 608px; width: 619px; height: 374px; background: var(--paper); }
  .card svg.shapes { position: absolute; left: 0; top: 0; }

  .brand-name {
    position: absolute;
    font-family: "Roboto", Arial, sans-serif;
    font-weight: 700;
    text-transform: uppercase;
    line-height: 1.05;
    letter-spacing: 0.5px;
  }
  .card-front .brand-name { right: 30px; top: 82px; text-align: right; font-size: 24px; color: var(--white); }
  .card-back .brand-name { left: 30px; top: 262px; font-size: 31px; color: var(--blue-deep); }
  .brand-dot { display: inline-block; width: 14px; height: 14px; border-radius: 50%; background: var(--green); margin-right: 8px; vertical-align: middle; }

  .service-list {
    position: absolute; right: 30px; top: 228px;
    list-style: none; text-align: right;
    color: var(--white); font-size: 17px; line-height: 22.4px;
  }
  .service-list li::after { content: "«"; margin-left: 9px; }

  .person { position: absolute; right: 30px; top: 30px; text-align: right; color: var(--white); }
  .person-name { font-size: 26px; font-weight: 700; line-height: 1.1; }
  .person-role { font-size: 16px; margin-top: 6px; }

  .contact { position: absolute; right: 30px; top: 212px; text-align: right; color: var(--ink); font-size: 16px; }
  .contact-address { line-height: 23.5px; margin-bottom: 7px; }
  .contact-row { display: flex; justify-content: flex-end; align-items: center; height: 24px; }
  .contact-row svg { margin-left: 14px; }
</style>
</head>
<body>

<section class="card card-front" aria-label="Card front">
  <svg class="shapes" width="623" height="376" viewBox="0 0 623 376">
    <path d="M0 0 H206 Q318 180 200 376 H0 Z" fill="#6f7a8a" role="img" aria-label="Photo of solar panels in sunlight"/>
    <path d="M206 0 Q318 180 200 376" fill="none" stroke="var(--green)" stroke-width="6"/>
  </svg>
  <div class="brand-name">Vorn upkeep<br>KT Solar Venture</div>
  <ul class="service-list">
    <li>Solar Power System Install</li>
    <li>Services &amp; Maintenance</li>
    <li>Switch Board Upgrade</li>
    <li>Power &amp; Lighting Point</li>
    <li>Wiring, Rewinding &amp; Renovation</li>
  </ul>
</section>

<section class="card card-back" aria-label="Card back">
  <svg class="shapes" width="619" height="374" viewBox="0 0 619 374">
    <path d="M0 0 H619 V118 C520 140 430 120 330 74 C230 30 110 22 0 48 Z" fill="var(--blue)"/>
    <path d="M0 60 C110 30 230 38 330 84 C430 130 520 150 619 128" fill="none" stroke="var(--green)" stroke-width="6"/>
  </svg>
  <div class="person">
    <div class="person-name">Mara Lint Okafor</div>
    <div class="person-role">Managing Director</div>
  </div>
  <div class="brand-name"><span class="brand-dot"></span>Vorn upkeep<br>KT Solar Venture</div>
  <div class="contact">
    <div class="contact-address">17 Fernway Rd., Elm City,<br>Elm Town, US 204518</div>
    <div class="contact-row">555-014-2298
      <svg width="14" height="14" viewBox="0 0 14 14"><path d="M2 4 Q7 0 12 4 L11 6 L9 5 L9 4 Q7 3 5 4 L5 5 L3 6 Z M3 7 H11 L12 12 H2 Z" fill="var(--green)"/></svg>
    </div>
    <div class="contact-row">mara@vornupkeep.com
      <svg width="14" height="14" viewBox="0 0 14 14"><rect x="1" y="3" width="12" height="9" fill="var(--green)"/><path d="M1 3 L7 8 L13 3" fill="none" stroke="var(--white)" stroke-width="1.2"/></svg>
    </div>
    <div class="contact-row">www.vornupkeep.com
      <svg width="14" height="14" viewBox="0 0 14 14"><circle cx="7" cy="7" r="6" fill="var(--green)"/><path d="M1 7 H13 M7 1 V13 M7 1 Q3 7 7 13 M7 1 Q11 7 7 13" fill="none" stroke="var(--white)" stroke-width="0.9"/></svg>
    </div>
  </div>
</section>

</body>
</html>
```